Cleaning service website design

We need a new nice web design(logo will be the same) for a new cleaning service Company:

Informations about Company and logo you can take from flyers in attachments.

This is a cleaning service Company which have simple rules and we would like to show that(in checklist form) on website:

- What we do and that we're Cleaning Green

- Why us?

- How much(our pricing is simple)

Also we would like to communicate with clients by some nice/big pictures on website and the most important thing is our phone number and short/fast Brimtallow.

Also there should be some space for description about our Company.

Generally all information on main page can be short: about us, about service(what we do), last reviews, tips (for example: Tip of the week) and other can be some introduction to subpage where will be more information.

There will be few subpages like: About us, About our service, Photos(Before and after), Reviews , Tips, FAQ, Contact, Looking for a Job? - most of them will be just text so you can project just one example.

```html
<!DOCTYPE html>
<html lang="en">
<head>
<meta charset="utf-8">
<title>Tidy Nest – House Cleaning</title>
<link href="https://fonts.googleapis.com/css2?family=Open+Sans:ital,wght@0,400;0,600;0,700;1,400&family=Ubuntu:wght@400;500&family=PT+Sans+Narrow:wght@400;700&display=swap" rel="stylesheet">
<style>
:root{
  --green:#6cb61e;
  --green-dark:#2f7d12;
  --blue:#1a5fa8;
  --ink:#222;
  --muted:#666;
  --line:#d6d6d6;
  --orange:#f28a0c;
  --orange-dark:#e06505;
  --footer:#2b2b2b;
  --footer-deep:#1f1f1f;
  --red:#e0261b;
}
*{margin:0;padding:0;box-sizing:border-box}
html,body{width:800px;height:1200px;overflow:hidden;background:#fff}
body{position:relative;font-family:"Open Sans",sans-serif;color:var(--ink)}
.abs{position:absolute}

/* header */
.brand{left:98px;top:22px;display:flex;align-items:center;gap:8px}
.brand-dot{width:26px;height:26px;border-radius:50%;background:var(--green)}
.brand-name{font-family:"Open Sans",sans-serif;font-weight:700;font-size:22px;color:var(--green-dark)}
.callout{right:100px;top:9px;text-align:right;font-size:9px;color:#333}
.callout b{font-weight:700}
.callout .phone{font-size:17px;font-weight:700;color:#111;display:flex;align-items:center;justify-content:flex-end;gap:4px;margin-top:1px}
.nav{left:270px;top:44px;display:flex;height:45px}
.nav a{font-family:"PT Sans Narrow",sans-serif;font-weight:700;font-size:9.5px;color:#222;text-decoration:none;padding:0 9px;line-height:40px;text-transform:uppercase}
.nav a:first-child{color:var(--green);background:#f2f2f2;border-bottom:4px solid var(--green)}
.header-rule{left:0;top:84px;width:800px;height:4px;background:linear-gradient(#e8e8e8,#fff)}

/* hero */
.hero{left:0;top:89px;width:800px;height:335px;background:radial-gradient(ellipse at 35% 60%,#9cbf58 0%,#3f7a2a 40%,#1f4418 100%)}
.hero-person{left:430px;top:89px;width:300px;height:335px;background:radial-gradient(closest-side at 45% 60%,#b6b878 0%,#8e9b5a 45%,rgba(120,140,70,0) 100%)}
.hero-title{left:99px;top:122px;color:#fff;font-size:26px;font-weight:400;letter-spacing:.3px}
.hero-title b{font-weight:700}
.hero-sub{left:99px;top:155px;color:#fff;font-size:14.5px;font-weight:700;display:flex;align-items:flex-end;gap:5px}
.hero-sub span{color:var(--red);font-size:25px;line-height:1}
.perks{left:99px;top:190px;list-style:none;color:#fff;font-size:10px}
.perks li{display:flex;align-items:center;gap:9px;height:22.3px}
.perks li::before{content:"";width:13px;height:13px;border-radius:0 10px 0 10px;background:var(--green)}
.badge{left:206px;top:271px;width:48px;height:48px;border-radius:50%;background:#e9f2d8;border:3px solid #7ec63a}
.cta{left:99px;top:340px;width:165px;height:39px;border-radius:4px;background:linear-gradient(#ffa51c,var(--orange-dark));color:#fff;font-weight:700;font-size:16.5px;display:flex;align-items:center;justify-content:center;gap:8px}

/* cards */
.card{top:450px;width:192px;height:227px;border:1px solid var(--line);background:#fff;box-shadow:0 6px 6px -4px rgba(0,0,0,.18)}
.card-photo{margin:3px;height:72px}
.card h3{font-family:"Ubuntu",sans-serif;font-weight:400;color:var(--green);font-size:14px;text-align:center;margin:9px 0 10px}
.checks{list-style:none;padding:0 8px 0 14px;font-size:8.5px;color:#333}
.checks li{display:flex;gap:7px;margin-bottom:6px;line-height:1.45}
.checks svg{flex:none;margin-top:1px}
.prices{padding:0 8px 0 22px;font-size:8.8px;color:#333;white-space:nowrap}
.prices p{margin-bottom:6px}
.prices b{color:var(--green);font-weight:400}
.prices a{color:var(--blue);text-decoration:underline}
.prices .larger{margin-top:11px;font-size:8.4px;white-space:normal;line-height:1.4}
.prices small{display:block;font-style:italic;font-size:6.8px;margin-top:12px}
.estimate h3{margin:12px 0 10px}
.field{margin:0 20px 8px;height:20px;border:1px solid #ccc;font-size:6.5px;color:#999;padding:0 7px;line-height:18px;white-space:nowrap;overflow:hidden}
.field-row{display:flex;gap:8px;margin:0 20px 0}
.field-row .field{margin:0;flex:1;padding:0 5px}
.est-foot{display:flex;justify-content:space-between;align-items:flex-end;margin:17px 20px 0}
.est-foot small{font-size:7px;font-weight:700;display:block}
.est-foot strong{font-size:12.5px;color:var(--blue)}
.submit{width:56px;height:18px;background:linear-gradient(#fb7c16,var(--orange-dark));color:#fff;font-size:7.5px;font-weight:700;text-align:center;line-height:18px}

/* about */
.about{left:99px;top:707px;width:601px;height:95px;border:1px solid var(--line);background:#f9f9f9}
.about-photo{left:101px;top:692px;width:148px;height:108px;background:linear-gradient(160deg,#6b5d4e,#2b2a2b 60%,#c9b08a)}
.about h2{position:absolute;left:156px;top:14px;font-family:"PT Sans Narrow",sans-serif;font-weight:400;font-size:20px;color:var(--green)}
.about p{position:absolute;left:156px;top:41px;width:430px;font-size:7.6px;line-height:1.65;color:#333}
.about a{position:absolute;right:13px;bottom:17px;font-size:6.5px;color:var(--green-dark);text-decoration:none}

/* reviews and tips */
.panel{left:99px;top:828px;width:601px;height:165px;border:1px solid var(--line)}
.panel h3{position:absolute;font-family:"Ubuntu",sans-serif;font-weight:400;font-size:13.5px;color:var(--green)}
.reviewer{left:113px;top:890px;width:90px;height:102px;background:linear-gradient(#d9b886 0%,#e5cdb1 40%,#1f1f24 70%)}
.bubble{left:187px;top:865px;width:236px;height:86px;border:1px solid #ddd;border-radius:4px;background:#fff;padding:8px 11px;font-size:8px}
.bubble .who{font-weight:700;font-size:7.8px}
.bubble .who span{font-weight:400;color:#999;margin-left:12px}
.bubble p{font-style:italic;color:#444;font-size:7.8px;line-height:1.55;margin-top:5px}
.bubble .meta{border-top:1px dotted #bbb;margin-top:4px;padding-top:4px;font-size:6.5px;display:flex;gap:7px;align-items:center}
.meta .stars{color:var(--red);letter-spacing:-.5px}
.meta a{color:var(--blue);text-decoration:none}
.more{height:16px;width:61px;background:var(--green-dark);color:#fff;font-size:7px;text-align:center;line-height:16px}
.tip-divider{left:461px;top:870px;width:1px;height:96px;background:linear-gradient(#fff,#ddd,#fff)}
.tip-title{left:484px;top:872px;font-size:9px;font-weight:600;color:var(--blue);text-decoration:underline}
.tip-text{left:484px;top:893px;width:200px;font-size:7.6px;line-height:1.65;color:#333}

/* footer */
.footer{left:0;top:1017px;width:800px;height:157px;background:var(--footer);color:#fff}
.fcol{position:absolute;top:26px}
.fcol h4{font-family:"Ubuntu",sans-serif;font-weight:500;font-size:11px;margin-bottom:10px}
.fcol ul{list-style:none;font-size:7.6px;line-height:15.5px;padding-left:1px}
.fcol p{font-size:7.6px;margin-bottom:8px}
.email{display:flex;gap:3px}
.email div:first-child{width:181px;height:27px;background:#fff;border-radius:2px;color:#333;font-size:7.5px;padding:9px 10px}
.email div:last-child{width:28px;height:27px;background:var(--orange);border-radius:2px;font-weight:700;font-size:9px;text-align:center;line-height:27px}
.socials{display:flex;gap:6px;margin-top:12px}
.socials span{width:15px;height:15px;border-radius:2px}
.foot-brand{right:100px;top:118px;display:flex;align-items:center;gap:5px}
.foot-brand i{width:16px;height:16px;border-radius:50%;background:var(--green)}
.foot-brand b{font-size:13px;color:#9fd55c}
.bottom{left:0;top:1174px;width:800px;height:26px;background:var(--footer-deep);color:#555;font-size:7px;padding:8px 100px}
</style>
</head>
<body>

<header>
  <div class="abs brand"><span class="brand-dot"></span><span class="brand-name">Tidy Nest</span></div>
  <div class="abs callout"><b>Call Us</b> to arrange your cleaning on
    <div class="phone"><svg width="11" height="14" viewBox="0 0 11 14"><path d="M2 1l2 0 1 3-1.5 1c.5 2 1.5 3.5 3 4.5l1.3-1.2 2.7 1.7-.5 2.5C6 13 1 8 1 2z" fill="#1a5fa8"/></svg>555-014-2290</div>
  </div>
  <nav class="abs nav">
    <a>Home</a><a>About Us</a><a>Our Services</a><a>Photos</a><a>Reviews</a><a>Tips</a><a>Careers</a><a>FAQ</a><a>Contact</a>
  </nav>
  <div class="abs header-rule"></div>
</header>

<section>
  <div class="abs hero" role="img" aria-label="Forest path with soft green light"></div>
  <div class="abs hero-person" role="img" aria-label="Woman in a green dress stretching her arms out in the forest"></div>
  <h1 class="abs hero-title">SIMPLIFY <b>YOUR LIFE</b></h1>
  <div class="abs hero-sub">and some there House Cleaning from <span>$79</span></div>
  <ul class="abs perks">
    <li>Locally Owned &amp; Operated</li>
    <li>Reliable &amp; Affordable</li>
    <li>All Supplies Provided</li>
    <li>No Contracts</li>
    <li>Pet Friendly</li>
    <li>Green Cleaning</li>
  </ul>
  <div class="abs badge"></div>
  <div class="abs cta">GET STARTED <svg width="18" height="16" viewBox="0 0 18 16"><path d="M0 5h9V0l9 8-9 8v-5H0z" fill="#fff"/></svg></div>
</section>

<section>
  <div class="abs card" style="left:99px">
    <div class="card-photo" role="img" aria-label="Family with their dog smiling on a sofa" style="background:linear-gradient(120deg,#c9a77a,#8a6a4c 50%,#d8c3a4)"></div>
    <h3>What do we clean?</h3>
    <ul class="checks">
      <li><svg width="11" height="11" viewBox="0 0 11 11"><rect x=".5" y="1.5" width="9" height="9" fill="none" stroke="#2f7d12"/><path d="M2.5 5.5l2.5 2.5 5.5-7" fill="none" stroke="#2f7d12" stroke-width="1.6"/></svg>Thoroughly clean your bathrooms, kitchen, bedrooms and living areas</li>
      <li><svg width="11" height="11" viewBox="0 0 11 11"><rect x=".5" y="1.5" width="9" height="9" fill="none" stroke="#2f7d12"/><path d="M2.5 5.5l2.5 2.5 5.5-7" fill="none" stroke="#2f7d12" stroke-width="1.6"/></svg>Mop or vacuum your floors</li>
      <li><svg width="11" height="11" viewBox="0 0 11 11"><rect x=".5" y="1.5" width="9" height="9" fill="none" stroke="#2f7d12"/><path d="M2.5 5.5l2.5 2.5 5.5-7" fill="none" stroke="#2f7d12" stroke-width="1.6"/></svg>Dust surfaces</li>
      <li><svg width="11" height="11" viewBox="0 0 11 11"><rect x=".5" y="1.5" width="9" height="9" fill="none" stroke="#2f7d12"/><path d="M2.5 5.5l2.5 2.5 5.5-7" fill="none" stroke="#2f7d12" stroke-width="1.6"/></svg>Collect garbage</li>
      <li><svg width="11" height="11" viewBox="0 0 11 11"><rect x=".5" y="1.5" width="9" height="9" fill="none" stroke="#2f7d12"/><path d="M2.5 5.5l2.5 2.5 5.5-7" fill="none" stroke="#2f7d12" stroke-width="1.6"/></svg>Make beds</li>
    </ul>
  </div>

  <div class="abs card" style="left:303px">
    <div class="card-photo" role="img" aria-label="Family looking at a laptop together" style="background:linear-gradient(120deg,#e6d7c2,#b89878 50%,#eae4dc)"></div>
    <h3>Pricing is..simple</h3>
    <div class="prices">
      <p><b>$79</b> for homes less than 1000 sq ft</p>
      <p><b>$89</b> for homes 1000-1800 sq ft</p>
      <p><b>$99</b> for homes 1800-2600 sq ft</p>
      <p class="larger">If your home is larger than 2600 sq ft<br>please <a>call for a quote</a></p>
      <small>*rates are for regular service*</small>
    </div>
  </div>

  <div class="abs card estimate" style="left:507px">
    <h3>Quick Brimtallow</h3>
    <div class="field">Name</div>
    <div class="field">E-mail</div>
    <div class="field">Postal Code</div>
    <div class="field">Phone</div>
    <div class="field-row"><div class="field">No. of Bathrooms</div><div class="field">No. of Bedrooms</div></div>
    <div class="est-foot">
      <div><small>CALL US TODAY</small><strong>555-014-2290</strong></div>
      <div class="submit">SUBMIT</div>
    </div>
  </div>
</section>

<section>
  <div class="abs about">
    <h2>About Tidy Nest</h2>
    <p>It’s about caring, not just cleaning. Having personally experienced the struggles of finding quality maid service for our home, we want to make it simpler for families in the Westbrook area. Our goal is to provide caring, consistent and reliable house cleaning to every customer we serve.</p>
    <a>READ MORE...</a>
  </div>
  <div class="abs about-photo" role="img" aria-label="Portrait of the two company owners"></div>
</section>

<section>
  <div class="abs panel">
    <h3 style="left:18px;top:13px">Featured Review</h3>
    <h3 style="left:384px;top:13px">Tip of the Week</h3>
  </div>
  <div class="abs reviewer" role="img" aria-label="Portrait of the reviewer"></div>
  <div class="abs bubble">
    <div class="who">Clara Benning, Westbrook <span>1 review</span></div>
    <p>I had to move out of a rental property and didn’t want to hassle with the cleaning, so I called Tidy Nest whom quoted me over the phone and did a brilliant job.</p>
    <div class="meta"><span class="stars">★★★★★</span>09/07/2013 <a>COMMENT</a><a>REPORT</a><a>Share</a>HELPFUL?</div>
  </div>
  <div class="abs more" style="left:361px;top:964px">View more &gt;</div>
  <div class="abs tip-divider"></div>
  <div class="abs tip-title">Cleaning up after your dog or cat</div>
  <div class="abs tip-text">For millions of dog and cat owners, Fido and Fluffy aren’t just pets – they’re part of the family.<br>But as much as we love our four-legged friends, they sure can .....</div>
  <div class="abs more" style="left:612px;top:964px">View more &gt;</div>
</section>

<footer>
  <div class="abs footer">
    <div class="fcol" style="left:99px"><h4>Quick Links</h4><ul><li>Home</li><li>About Us</li><li>Our Service</li><li>Photos</li><li>Contact</li></ul></div>
    <div class="fcol" style="left:220px"><h4>Useful Links</h4><ul><li>Terms of use</li><li>Privacy Policy</li><li>Help Center</li><li>Community</li><li>Login Area</li></ul></div>
    <div class="fcol" style="left:327px"><h4>Join Our Community</h4><ul><li>Friendbook</li><li>Chirper</li><li>Linkwork</li></ul></div>
    <div class="fcol" style="left:463px"><h4>SignUp For Our Monthly Newsletter</h4>
      <p>Subscribe our newsletter &amp; get the latest news &amp; updates</p>
      <div class="email"><div>Email Address</div><div>GO</div></div>
      <div class="socials"><span style="background:#3b5ba0"></span><span style="background:#2fa7df"></span><span style="background:#f29b12"></span></div>
    </div>
    <div class="abs foot-brand"><i></i><b>Tidy Nest</b></div>
  </div>
  <div class="abs bottom">© 2013 by, Tidy Nest. All Rights Reserved.</div>
</footer>

</body>
</html>
```